Counseling Practice Business Card

I need a professional looking business card incorporating my new logo that was just completed. Card needs to incorporate my name and title, description of my specialty, my address, my phone number, my fax number, my email and my website URL. I need to be able to choose design on/with different paper colors and textures.
I do not have a lot of business card ideas so I am open to anything but I want bold,sharp, clear card without additional designs other than my logo (see attached file info). I am open to different color backgrounds or paper colors including black. I do not like traditional brackets around area codes in phone number or dashes between numbers in phone number. Am open to other ways of presenting including periods between numbers as appropriate. I do not know enough to know what I like yet but I want card to coordinate and work together with my logo. My practice emphasizes natural mental health interventions so any use of color (with background paper color or the blue and green in my logo) that elicits nature is nice. In addition to black, any natural brown or wood looking background might be desirable also. Most of the offerings so far look very similar and boring.

Target Market(s)

Potential therapy clients and other professionals

Contact Information for Business Card

Card information:
Gerald M. Whitcombe, Ph.D.
Licensed Clinical Psychologist
Integrative Health Coach
4812 Marlowe Ridge Blvd SE
Suite 310
Fernbrook, GA 30482
(770) 415-2983 phone
(770) 581-4096 fax
drgeraldwhitcombe@quillmarsh.net
brightfernwellness.net

Font styles to use
Serif
Sans Serif
Other font styles liked:
• anything that you think looks crisp, clear and easily readable

Requirements
Must have
• Any color used should coordinate with my logo design (see attached files).
• Card should be printed horizontally so top and bottom are longest sides of rectangle.
• Background color or paper color should complement and highlight logo. Do not like a white background. black, grey, brown or any color my logo would blend well with.
Nice to have
• I would like designer to utilize color to highlight letters/name or phone-fax-web symbols.
• Bottom edge of card could be highlighted if appropriate to an idea.
Should not have
• I would NOT want the card to have a pure white background at all.
• No clear cards.
• Cards should be oriented with long sides on bottom and top, NOT sides. DO NOT LIKE THIS THIN TALL ORIENTATION.

```html
<!DOCTYPE html>
<html lang="en">
<head>
<meta charset="UTF-8">
<title>Brightfern Wellness – Business Card</title>
<link rel="stylesheet" href="https://fonts.googleapis.com/css2?family=Open+Sans:wght@600;700&family=Tinos&display=swap">
<style>
  :root {
    --backdrop: #bcc2c3;
    --paper: #a6a6a8;
    --ink: #141414;
    --brand-green: #1f7a3e;
    --brand-blue: #2f86cc;
    --shadow: rgba(40, 48, 52, 0.28);
  }
  * { box-sizing: border-box; margin: 0; padding: 0; }
  html, body {
    width: 1200px;
    height: 824px;
    overflow: hidden;
    background: var(--backdrop);
  }
  .canvas {
    width: 1200px;
    height: 824px;
    display: flex;
    align-items: center;
    justify-content: center;
    gap: 40px;
  }
  .card {
    position: relative;
    width: 560px;
    height: 320px;
    background: var(--paper);
    box-shadow: 0 10px 24px var(--shadow);
  }
  .brand {
    position: absolute;
    display: flex;
    align-items: center;
    gap: 8px;
    font-family: "Open Sans", Arial, sans-serif;
    font-weight: 700;
    color: var(--brand-green);
    white-space: nowrap;
  }
  .brand-dot {
    flex: none;
    border-radius: 50%;
    background: var(--brand-blue);
  }
  .card-front .brand {
    left: 30px;
    top: 114px;
    font-size: 20px;
  }
  .card-front .brand-dot { width: 16px; height: 16px; }

  .contact {
    position: absolute;
    left: 300px;
    top: 92px;
    font-family: "Tinos", "Times New Roman", serif;
    font-size: 13.5px;
    line-height: 1.22;
    color: var(--ink);
    white-space: nowrap;
  }
  .contact-name {
    font-family: "Open Sans", Arial, sans-serif;
    font-weight: 700;
    font-size: 15px;
    line-height: 1.3;
  }
  .contact-group { margin-top: 8px; }
  .contact-group:first-of-type { margin-top: 0; }

  .card-back .brand {
    left: 50%;
    top: 50%;
    transform: translate(-50%, -50%);
    font-size: 38px;
    gap: 14px;
  }
  .card-back .brand-dot { width: 26px; height: 26px; }
</style>
</head>
<body>
  <main class="canvas">
    <section class="card card-front" aria-label="Business card front">
      <div class="brand">
        <span class="brand-dot"></span>
        <span class="brand-name">Brightfern Wellness</span>
      </div>
      <div class="contact">
        <div class="contact-group">
          <p class="contact-name">Gerald M. Whitcombe, Ph.D.</p>
          <p class="contact-title">Licensed Clinical Psychologist</p>
          <p class="contact-title">Integrative Health Coach</p>
        </div>
        <div class="contact-group">
          <p>4812 Marlowe Ridge Blvd SE</p>
          <p>Suite 310</p>
          <p>Fernbrook, GA 30482</p>
        </div>
        <div class="contact-group">
          <p>(770) 415-2983 phone</p>
          <p>(770) 581-4096 fax</p>
          <p>drgeraldwhitcombe@quillmarsh.net</p>
          <p>brightfernwellness.net</p>
        </div>
      </div>
    </section>

    <section class="card card-back" aria-label="Business card back">
      <div class="brand">
        <span class="brand-dot"></span>
        <span class="brand-name">Brightfern Wellness</span>
      </div>
    </section>
  </main>
</body>
</html>
```